Real Estate Business Card

On the front side I want to have my info, my brokerage info.
On the back side I want have my complany’s logo, website and Facebook link. I will provide all this once I select a design.

I would like to see Black background and gold text, Dark Blue and gold text and White and blue text designs

Font styles to use
Sans Serif
Script

```html
<!DOCTYPE html>
<html lang="en">
<head>
<meta charset="utf-8">
<title>Northgate Real Estate – Business Card</title>
<link href="https://fonts.googleapis.com/css2?family=Montserrat:wght@700;800&family=Roboto:wght@400;500;700&display=swap" rel="stylesheet">
<style>
  :root {
    --backdrop: #2b2b2d;
    --card: #1f1f21;
    --red: #d9343a;
    --slate: #7d8597;
    --logo-grey: #4a4e59;
    --gold: #f1cf5f;
    --white: #f4f4f4;
    --divider: #8a8a8a;
  }
  * { box-sizing: border-box; margin: 0; padding: 0; }
  html, body { width: 1200px; height: 900px; overflow: hidden; }
  body {
    background: var(--backdrop);
    font-family: "Roboto", Arial, sans-serif;
    position: relative;
  }
  .card {
    position: absolute;
    width: 700px;
    height: 400px;
    background: var(--card);
    box-shadow: 0 10px 30px rgba(0,0,0,.45);
    overflow: hidden;
  }
  /* Back side */
  .card--back { left: 320px; top: 30px; }
  .back-brand {
    position: absolute;
    right: 60px;
    bottom: 60px;
    display: flex;
    align-items: center;
    gap: 14px;
  }
  .brand-square { width: 26px; height: 26px; background: var(--red); }
  .back-brand .brand-name {
    font-family: "Montserrat", Arial, sans-serif;
    font-weight: 800;
    font-size: 38px;
    color: var(--red);
    letter-spacing: 1px;
  }
  /* Front side */
  .card--front { left: 180px; top: 470px; }
  .front-brand {
    position: absolute;
    left: 40px;
    top: 150px;
    width: 330px;
    display: flex;
    align-items: center;
    justify-content: center;
    gap: 12px;
  }
  .front-brand .brand-name {
    font-family: "Montserrat", Arial, sans-serif;
    font-weight: 800;
    font-size: 40px;
    color: var(--logo-grey);
  }
  .divider {
    position: absolute;
    left: 410px;
    top: 40px;
    width: 2px;
    height: 280px;
    background: linear-gradient(to bottom, transparent, var(--divider) 30%, var(--divider) 70%, transparent);
  }
  .contact {
    position: absolute;
    left: 440px;
    top: 50px;
    color: var(--white);
  }
  .person-name {
    font-family: "Montserrat", Arial, sans-serif;
    font-weight: 700;
    font-size: 24px;
    color: var(--gold);
    line-height: 1;
  }
  .person-title {
    font-weight: 500;
    font-size: 17px;
    color: var(--red);
    margin-top: 2px;
  }
  .address {
    font-size: 16px;
    line-height: 1.3;
    margin-top: 16px;
  }
  .contact-list { list-style: none; margin-top: 12px; }
  .contact-list li {
    display: flex;
    align-items: center;
    gap: 10px;
    font-size: 16px;
    line-height: 1.5;
  }
  .contact-list svg { width: 14px; height: 14px; flex: none; fill: var(--gold); }
  .edge-band {
    position: absolute;
    left: 0; bottom: 0;
    width: 100%;
    height: 9px;
    display: flex;
  }
  .edge-band .red { width: 58%; background: var(--red); }
  .edge-band .slate { flex: 1; background: var(--slate); }
</style>
</head>
<body>

<section class="card card--back" aria-label="Card back">
  <div class="back-brand">
    <span class="brand-square"></span>
    <span class="brand-name">Northgate</span>
  </div>
</section>

<section class="card card--front" aria-label="Card front">
  <div class="front-brand">
    <span class="brand-square"></span>
    <span class="brand-name">Northgate</span>
  </div>

  <div class="divider"></div>

  <div class="contact">
    <div class="person-name">DANIEL REYES</div>
    <div class="person-title">CEO/FOUNDER</div>
    <p class="address">2140 Willow Creek Road<br>Juneau, Alaska 34810</p>
    <ul class="contact-list">
      <li>
        <svg viewBox="0 0 16 16" aria-hidden="true"><path d="M3.5 1l3 3-1.7 1.7c.8 1.9 2.6 3.7 4.5 4.5L11 8.5l3 3-2 2.5C6.5 13.5 2.5 9.5 1 4z"/></svg>
        555 214 7730
      </li>
      <li>
        <svg viewBox="0 0 16 16" aria-hidden="true"><path d="M4 0h8a1 1 0 0 1 1 1v14a1 1 0 0 1-1 1H4a1 1 0 0 1-1-1V1a1 1 0 0 1 1-1zm1 2v10h6V2zm3 11a1 1 0 1 0 0 2 1 1 0 0 0 0-2z"/></svg>
        555 380 6142
      </li>
      <li>
        <svg viewBox="0 0 16 16" aria-hidden="true"><path d="M4 1h7v4H4zM1 6h14v7h-3v2H4v-2H1zm4 5v3h6v-3z"/></svg>
        555 907 3385
      </li>
      <li>
        <svg viewBox="0 0 16 16" aria-hidden="true"><path d="M0 3h16v10H0zm1.5 1.2L8 9l6.5-4.8V4h-13z"/></svg>
        daniel@northgate.com
      </li>
      <li>
        <svg viewBox="0 0 16 16" aria-hidden="true"><circle cx="8" cy="8" r="7"/></svg>
        www.northgate.com
      </li>
    </ul>
  </div>

  <div class="edge-band"><span class="red"></span><span class="slate"></span></div>
</section>

</body>
</html>
```